Verodex business card

Business card for sustainable investment company called "Verodex". Verodex is an exchange platform selling carbon credits between buyers and sellers. Carbon Credits are an environmental commodity for reducing global carbon emissions.

the card should obviously have our logo and the theme should be sustainability/environment mixed with a trading platform.

Contact Information for Business Card

Logo, Name, Title, Phone, Email

Colors
0054AA
0677BA
7BADD7
CADEEF
E8F1F8
0094D4
00A9DD
6FCCEA
C7EBF8
E9F6FB
00AB8E
00BBA5
67D7C9
C6EFE9
E9F9F6
59FF00
82FF00
B8FF75
E3FFCB
F4FFEA

```html
<!DOCTYPE html>
<html lang="en">
<head>
<meta charset="utf-8">
<title>Verodex business card</title>
<link href="https://fonts.googleapis.com/css2?family=Open+Sans:wght@400;600;700;800&display=swap" rel="stylesheet">
<style>
  :root {
    --card: #1f1f23;
    --card-deep: #17171a;
    --ink: #ffffff;
    --ink-soft: #e6e6ea;
    --accent: #4a9bd6;
    --accent-light: #5fc3e4;
    --accent-deep: #3a72c4;
    --stage: #e9ebee;
    --mark-faint: #2a2a2f;
  }
  * { box-sizing: border-box; margin: 0; padding: 0; }
  html, body { width: 1200px; height: 780px; overflow: hidden; }
  body {
    background: var(--stage);
    font-family: "Open Sans", Arial, sans-serif;
    position: relative;
  }
  .card {
    position: absolute;
    top: 235px;
    width: 540px;
    height: 310px;
    background: var(--card);
    border-bottom: 4px solid var(--accent-deep);
    overflow: hidden;
  }
  .card--front { left: 30px; }
  .card--back { left: 630px; }

  .brand {
    display: flex;
    align-items: center;
    gap: 12px;
    color: var(--ink);
    font-weight: 800;
    text-transform: uppercase;
    letter-spacing: 0.06em;
  }
  .brand__square { background: var(--accent); display: block; }

  .card--back .brand {
    position: absolute;
    left: 50%; top: 50%;
    transform: translate(-50%, -50%);
    font-size: 52px;
    gap: 20px;
  }
  .card--back .brand__square { width: 46px; height: 46px; }

  .card--front .brand {
    position: absolute;
    left: 28px; top: 26px;
    font-size: 27px;
  }
  .card--front .brand__square { width: 26px; height: 26px; }

  .contact {
    position: absolute;
    left: 28px; top: 96px;
    color: var(--ink-soft);
    font-size: 13px;
    line-height: 1.55;
    list-style: none;
  }
  .contact__address { margin-bottom: 4px; }
  .contact__item { display: flex; align-items: center; gap: 8px; }
  .contact__icon { width: 12px; height: 12px; flex: none; }

  .person {
    position: absolute;
    right: 42px; top: 118px;
    text-align: right;
  }
  .person__name {
    color: var(--accent);
    font-size: 28px;
    font-weight: 700;
    line-height: 1.1;
  }
  .person__title {
    color: var(--ink);
    font-size: 15px;
    margin-top: 4px;
  }
  .tab {
    position: absolute;
    right: 0; top: 126px;
    width: 22px; height: 44px;
    background: linear-gradient(180deg, var(--accent-light), var(--accent-deep));
  }

  .watermark-name {
    position: absolute;
    left: 150px; bottom: -22px;
    color: var(--mark-faint);
    font-size: 96px;
    font-weight: 800;
    text-transform: uppercase;
    letter-spacing: 0.04em;
    white-space: nowrap;
  }
</style>
</head>
<body>

  <section class="card card--front" aria-label="Business card, contact side">
    <div class="watermark-name" aria-hidden="true">Verodex</div>

    <div class="brand">
      <span class="brand__square"></span>
      <span class="brand__name">Verodex</span>
    </div>

    <ul class="contact">
      <li class="contact__address">4180 Linden Ave. Suite 310<br>Dayton, OH 45402</li>
      <li class="contact__item">
        <svg class="contact__icon" viewBox="0 0 12 12" aria-hidden="true">
          <path d="M2.5 1 L4.5 1 L5.2 3.6 L4 4.6 C4.6 6 6 7.4 7.4 8 L8.4 6.8 L11 7.5 L11 9.5 C11 10.3 10.3 11 9.5 11 C5 11 1 7 1 2.5 C1 1.7 1.7 1 2.5 1 Z" fill="var(--accent)"/>
        </svg>
        <span>(555) 214-7390</span>
      </li>
      <li class="contact__item">
        <svg class="contact__icon" viewBox="0 0 12 12" aria-hidden="true">
          <rect x="0.5" y="2.5" width="11" height="7.5" rx="1" fill="var(--accent)"/>
          <path d="M1 3 L6 7 L11 3" fill="none" stroke="var(--card)" stroke-width="1"/>
        </svg>
        <span>info@verodexmail.com</span>
      </li>
      <li class="contact__item">
        <svg class="contact__icon" viewBox="0 0 12 12" aria-hidden="true">
          <circle cx="6" cy="6" r="5.2" fill="var(--accent)"/>
          <path d="M1 6 H11 M6 0.8 C3.5 3.5 3.5 8.5 6 11.2 M6 0.8 C8.5 3.5 8.5 8.5 6 11.2" fill="none" stroke="var(--card)" stroke-width="0.8"/>
        </svg>
        <span>www.verodexmail.com</span>
      </li>
    </ul>

    <div class="person">
      <p class="person__name">Marta Holecova</p>
      <p class="person__title">Managing Director</p>
    </div>
    <div class="tab"></div>
  </section>

  <section class="card card--back" aria-label="Business card, brand side">
    <div class="brand">
      <span class="brand__square"></span>
      <span class="brand__name">Verodex</span>
    </div>
  </section>

</body>
</html>
```